Fundraising team needing letterhead for sponsorship and donations

I would like a design that relates to our team name Rosy Wheel Squad. We ride in an annual bicycle event that raises money that goes towards cancer research.We already have a team jersey designed which i have attached. The team name we would prefer to be in pink. Our team includes males and females. The logo also needs to relate to bike riding.

Industry/Entity Type

Event

Font styles to use
Sans Serif

```html
<!DOCTYPE html>
<html lang="en">
<head>
<meta charset="utf-8">
<title>Rosy Wheel Squad – Letterhead</title>
<link rel="stylesheet" href="https://fonts.googleapis.com/css2?family=Montserrat:ital,wght@0,500;0,700;0,800;1,600&family=Oswald:wght@400;500&display=swap">
<style>
  :root {
    --canvas: #eef0f3;
    --paper: #ffffff;
    --pink: #e4197a;
    --pink-soft: #f6c7dd;
    --pink-faint: #fbe6ef;
    --blue-deep: #2a7fd0;
    --blue-mid: #5aa6e6;
    --blue-light: #cfe6f8;
    --ink: #2b2b33;
    --ink-soft: #4a5566;
  }
  * { box-sizing: border-box; margin: 0; padding: 0; }
  html, body {
    width: 1200px; height: 1000px; overflow: hidden;
    background: var(--canvas);
    font-family: "Montserrat", Arial, sans-serif;
  }
  .letterhead {
    position: absolute; left: 270px; top: 38px;
    width: 660px; height: 924px;
    background: var(--paper);
    box-shadow: 0 6px 24px rgba(0,0,0,.18);
    overflow: hidden;
  }
  .wave { position: absolute; left: 0; width: 100%; display: block; }
  .wave--top { top: 0; height: 190px; }
  .wave--bottom { bottom: 0; height: 140px; }

  .brand { position: absolute; display: flex; align-items: center; gap: 8px; }
  .brand__dot { border-radius: 50%; flex: none; }
  .brand__name {
    font-weight: 800; text-transform: uppercase; line-height: 1;
    letter-spacing: .5px;
  }
  .brand--header { left: 26px; top: 34px; }
  .brand--header .brand__dot { width: 40px; height: 40px; background: var(--pink-soft); }
  .brand--header .brand__name { font-size: 15px; color: var(--pink); width: 110px; }

  .title {
    position: absolute; left: 250px; top: 88px;
    font-weight: 800; font-size: 30px; color: var(--pink);
    letter-spacing: .3px; white-space: nowrap;
  }

  .watermark {
    position: absolute; left: 50%; top: 430px; transform: translateX(-50%);
    display: flex; align-items: center; gap: 18px;
  }
  .watermark .brand__dot { width: 120px; height: 120px; background: var(--pink-faint); }
  .watermark .brand__name { font-size: 44px; color: #f1d9e4; width: 320px; }

  .tagline {
    position: absolute; left: 190px; bottom: 64px;
    font-style: italic; font-weight: 600; font-size: 13px; color: #2c5d93;
    white-space: nowrap;
  }
  .brand--footer { right: 26px; bottom: 46px; }
  .brand--footer .brand__dot { width: 30px; height: 30px; background: var(--blue-light); }
  .brand--footer .brand__name { font-size: 11px; color: var(--blue-deep); width: 70px; }

  .address, .contact {
    font-family: "Oswald", Arial, sans-serif; font-size: 8.5px;
    letter-spacing: .3px; color: var(--ink); text-transform: uppercase;
    white-space: nowrap; line-height: 1;
  }
  .address { position: absolute; left: 30px; bottom: 86px; }
  .contact {
    position: absolute; right: 26px; bottom: 18px;
    display: flex; align-items: center; gap: 22px;
  }
  .contact__item { display: flex; align-items: center; gap: 5px; }
  .contact__icon { width: 11px; height: 11px; flex: none; }
</style>
</head>
<body>
  <main class="letterhead">
    <svg class="wave wave--top" viewBox="0 0 660 190" preserveAspectRatio="none" aria-hidden="true">
      <defs>
        <linearGradient id="topBlue" x1="0" y1="0" x2="1" y2="0">
          <stop offset="0" stop-color="#9ccbef"/>
          <stop offset=".5" stop-color="#4f9be0"/>
          <stop offset="1" stop-color="#2a7fd0"/>
        </linearGradient>
      </defs>
      <path d="M0 0 H660 V120 C560 60 430 40 300 50 C180 60 80 40 0 20 Z" fill="url(#topBlue)" opacity=".85"/>
      <path d="M0 28 C120 60 260 70 400 60 C500 54 590 80 660 130 V150 C580 100 470 84 360 90 C220 98 100 80 0 50 Z" fill="#cfe6f8" opacity=".9"/>
      <path d="M180 180 C300 140 470 120 660 160 V172 C480 140 320 150 180 190 Z" fill="#7ab7ea" opacity=".6"/>
    </svg>

    <div class="brand brand--header">
      <span class="brand__dot"></span>
      <span class="brand__name">Rosy Wheel Squad</span>
    </div>
    <h1 class="title">Rosy Wheel Squad</h1>

    <div class="watermark" aria-hidden="true">
      <span class="brand__dot"></span>
      <span class="brand__name">Rosy Wheel Squad</span>
    </div>

    <svg class="wave wave--bottom" viewBox="0 0 660 140" preserveAspectRatio="none" aria-hidden="true">
      <defs>
        <linearGradient id="bottomBlue" x1="0" y1="0" x2="1" y2="0">
          <stop offset="0" stop-color="#3d8fdc"/>
          <stop offset=".5" stop-color="#8ec4ee"/>
          <stop offset="1" stop-color="#3d8fdc"/>
        </linearGradient>
      </defs>
      <path d="M0 40 C160 70 380 60 660 0 V140 H0 Z" fill="url(#bottomBlue)" opacity=".85"/>
      <path d="M0 62 C200 90 420 70 660 30 V60 C420 96 200 110 0 86 Z" fill="#e4f1fb" opacity=".9"/>
      <rect x="0" y="112" width="660" height="28" fill="#ffffff"/>
    </svg>

    <p class="address">Name of the organization, Address line 1, Address line 2, City &amp; Zip code</p>
    <p class="tagline">Fundraising Bike Ride for Cancer Research</p>
    <div class="brand brand--footer">
      <span class="brand__dot"></span>
      <span class="brand__name">Rosy Wheel Squad</span>
    </div>

    <footer class="contact">
      <span class="contact__item">
        <svg class="contact__icon" viewBox="0 0 12 12" aria-hidden="true"><circle cx="6" cy="6" r="5.5" fill="none" stroke="#2b2b33"/><path d="M4 3.5 L5 3.2 L5.6 4.8 L5 5.3 C5.4 6.2 5.8 6.6 6.7 7 L7.2 6.4 L8.8 7 L8.5 8 C6 8.3 3.7 6 4 3.5 Z" fill="#2b2b33"/></svg>
        0400 123 456
      </span>
      <span class="contact__item">
        <svg class="contact__icon" viewBox="0 0 12 12" aria-hidden="true"><circle cx="6" cy="6" r="5.5" fill="none" stroke="#2b2b33"/><path d="M1 6 H11 M6 .5 C3.5 3 3.5 9 6 11.5 M6 .5 C8.5 3 8.5 9 6 11.5" fill="none" stroke="#2b2b33" stroke-width=".8"/></svg>
        www.rosywheelsquad.org
      </span>
      <span class="contact__item">
        <svg class="contact__icon" viewBox="0 0 12 12" aria-hidden="true"><circle cx="6" cy="6" r="5.5" fill="none" stroke="#2b2b33"/><rect x="3" y="4" width="6" height="4.2" fill="none" stroke="#2b2b33" stroke-width=".8"/><path d="M3 4 L6 6.4 L9 4" fill="none" stroke="#2b2b33" stroke-width=".8"/></svg>
        hello@rosywheelsquad.org
      </span>
    </footer>
  </main>
</body>
</html>
```